Web Design

We need a website for a company based in Doha Qatar called
Lumara Maid Service.

It is the number one maid cleaning service company, and we have branches all over qatar.

Luxury Cleaning Service Provider.

The color scheme is gold, yellow and black like the logo.

Before they get to the website, there is an intro video.

The website should depict luxury.

Target Market(s)

People who need maids at their houses.

Industry/Entity Type

Cleaning Service

Requirements
Must have
• Luxury, Sleek, Modern

The opening sequence is a video which I already have. Its too big to upload here so I am going to put it on youtube.

After the opening sequence, the home page should have a widescreen photo background and it should change every five seconds, the first background photo should be of qatar westbay skyline. Then the second background should be of maid photos in cleaning positions. Then the third background should be of cleaner photos etc.

We will send you all the tabs and all the content later.

```html
<!DOCTYPE html>
<html lang="en">
<head>
<meta charset="utf-8">
<title>Lumara Maid Service</title>
<link href="https://fonts.googleapis.com/css2?family=Open+Sans:wght@300;400;600;700&display=swap" rel="stylesheet">
<style>
:root{
  --black:#000;
  --footer:#0b0b0b;
  --gold:#f7b83a;
  --gold-nav:#f2b640;
  --band-top:#e4ad48;
  --band-bottom:#d9a23f;
  --tab:#3a2a12;
  --ink:#1d1d1d;
  --muted:#9a9a9a;
  --panel:#f1f1f1;
  --rule:#e2e2e2;
  --white:#fff;
}
*{box-sizing:border-box;margin:0;padding:0}
html,body{width:1200px;height:1138px;overflow:hidden;background:var(--white)}
body{font-family:"Open Sans",Arial,sans-serif;color:var(--ink);position:relative}
.abs{position:absolute}

/* header */
.site-header{position:absolute;left:0;top:0;width:1200px;height:126px;background:var(--black)}
.brand{left:182px;top:48px;display:flex;align-items:center;gap:10px}
.brand-mark{width:34px;height:34px;border-radius:50%;background:var(--gold)}
.brand-name{font-size:19px;font-weight:400;color:var(--gold)}
.search{left:870px;top:15px;width:149px;height:41px;background:var(--white);display:flex;align-items:center;padding-left:12px;gap:8px;font-size:12px;color:#b5b5b5}
.main-nav{left:536px;top:69px;height:57px;display:flex}
.main-nav a{font-size:13px;color:var(--gold-nav);text-decoration:none;display:flex;align-items:center;height:57px}
.main-nav .current{background:var(--tab);border-top:3px solid var(--gold);width:66px;justify-content:center}
.main-nav a:nth-child(2){margin-left:38px}
.main-nav a:nth-child(3){margin-left:56px}
.main-nav a:nth-child(4){margin-left:56px}
.main-nav a:nth-child(5){margin-left:56px}

/* hero */
.hero{left:0;top:126px;width:1200px;height:343px;background:linear-gradient(180deg,#b8c6d6 0%,#c9d3dc 35%,#8e9aa6 62%,#7a8a94 76%,#4f6a78 86%,#5f7b88 100%)}
.hero-copy{right:179px;top:212px;text-align:right;color:#161616}
.hero-copy h1{font-size:22px;font-weight:400;line-height:26px}
.hero-copy p{font-size:14.5px;line-height:20px;margin-top:4px}
.btn-quote{right:181px;top:308px;width:90px;height:43px;background:var(--gold);color:#1a1a1a;font-size:14px;display:flex;align-items:center;justify-content:center;box-shadow:0 2px 4px rgba(0,0,0,.25)}

/* service band */
.service-band{left:0;top:469px;width:1200px;height:160px;background:linear-gradient(180deg,var(--band-top),var(--band-bottom))}
.service{position:absolute;top:19px}
.service .icon{position:absolute;left:0;top:0;width:72px;height:72px;border-radius:50%;background:var(--white);box-shadow:0 2px 4px rgba(0,0,0,.2);display:flex;align-items:center;justify-content:center}
.service h3{position:absolute;left:95px;top:19px;width:140px;font-size:16px;font-weight:400;line-height:20.5px;color:var(--white)}
.service p{position:absolute;left:95px;top:70px;width:126px;font-size:11px;line-height:15.5px;color:var(--white)}

/* welcome */
.welcome h2{left:182px;top:655px;font-size:21px;font-weight:400}
.welcome p{left:182px;top:701px;width:500px;font-size:11px;line-height:20.5px;color:var(--muted)}
.finder{left:769px;top:663px;width:250px;height:123px;background:var(--panel)}
.finder h3{position:absolute;left:25px;top:12px;font-size:15.5px;font-weight:400;line-height:20px}
.finder .postcode{position:absolute;left:26px;top:64px;width:126px;height:42px;background:var(--white);font-size:12px;display:flex;align-items:center;padding-left:12px}
.finder .go{position:absolute;left:157px;top:64px;width:66px;height:42px;background:var(--gold);font-size:14px;font-weight:700;display:flex;align-items:center;justify-content:center;box-shadow:1px 2px 3px rgba(0,0,0,.2)}
.rule{left:180px;top:812px;width:839px;height:1px;background:var(--rule)}

/* recent */
.recent-title{left:180px;top:826px;font-size:21px;font-weight:400}
.card{position:absolute;top:876px;width:194px}
.card .photo{width:194px;height:114px;background:linear-gradient(160deg,#b9b6ad,#8d8a82 60%,#6d6a63)}
.card h4{margin-top:8px;font-size:13px;font-weight:600}
.card span{display:block;font-size:10.5px;color:#a9a9a9;margin-top:1px}

/* footer */
.site-footer{left:0;top:1053px;width:1200px;height:85px;background:var(--footer)}
.foot-nav a{position:absolute;top:24px;font-size:13px;color:#d8d8d8;text-decoration:none}
.foot-nav a.current{color:var(--gold)}
.copyright{left:180px;top:47px;font-size:11px;color:#bdbdbd}
.social{position:absolute;top:29px;width:31px;height:31px;border-radius:50%;background:var(--white)}
</style>
</head>
<body>

<header class="site-header">
  <div class="abs brand"><span class="brand-mark"></span><span class="brand-name">Lumara Maid Service</span></div>
  <div class="abs search">
    <svg width="13" height="13" viewBox="0 0 13 13"><circle cx="5.5" cy="5.5" r="4" fill="none" stroke="#bbb" stroke-width="1.6"/><line x1="8.5" y1="8.5" x2="12" y2="12" stroke="#bbb" stroke-width="1.8"/></svg>
    Search
  </div>
  <nav class="abs main-nav">
    <a class="current" href="#">Home</a>
    <a href="#">About us</a>
    <a href="#">Services</a>
    <a href="#">Recent News</a>
    <a href="#">Contact</a>
  </nav>
</header>

<section class="abs hero" role="img" aria-label="Photo of the Doha West Bay skyline across the water">
  <svg class="abs" style="left:138px;top:140px" width="28" height="52" viewBox="0 0 28 52"><polyline points="26,2 2,26 26,50" fill="none" stroke="#fff" stroke-width="1.5"/></svg>
  <svg class="abs" style="left:1038px;top:140px" width="28" height="52" viewBox="0 0 28 52"><polyline points="2,2 26,26 2,50" fill="none" stroke="#fff" stroke-width="1.5"/></svg>
</section>
<div class="abs hero-copy">
  <h1>We are a very famous cleaning<br>company in Qatar</h1>
  <p>and have branches all over</p>
</div>
<a class="abs btn-quote">Get Quote</a>

<section class="abs service-band">
  <svg class="abs" style="left:145px;top:73px" width="12" height="14" viewBox="0 0 12 14"><polyline points="10,1 3,7 10,13" fill="none" stroke="#fff" stroke-width="3"/></svg>
  <svg class="abs" style="left:1042px;top:73px" width="12" height="14" viewBox="0 0 12 14"><polyline points="2,1 9,7 2,13" fill="none" stroke="#fff" stroke-width="3"/></svg>

  <div class="service" style="left:180px">
    <div class="icon"><svg width="32" height="44" viewBox="0 0 32 44"><rect x="6" y="2" width="20" height="38" fill="#111"/><rect x="2" y="40" width="28" height="3" fill="#111"/><g fill="#fff"><rect x="10" y="7" width="4" height="4"/><rect x="18" y="7" width="4" height="4"/><rect x="10" y="15" width="4" height="4"/><rect x="18" y="15" width="4" height="4"/><rect x="10" y="23" width="4" height="4"/><rect x="18" y="23" width="4" height="4"/><rect x="13" y="31" width="6" height="9"/></g></svg></div>
    <h3>Apartment<br>Cleaning</h3>
    <p>Whether you are moving out, planning a big party,</p>
  </div>
  <div class="service" style="left:493px">
    <div class="icon"><svg width="44" height="36" viewBox="0 0 44 36"><rect x="14" y="2" width="16" height="32" fill="#111"/><rect x="2" y="12" width="12" height="22" fill="#111"/><rect x="30" y="16" width="12" height="18" fill="#111"/><g fill="#fff"><rect x="17" y="6" width="3" height="3"/><rect x="24" y="6" width="3" height="3"/><rect x="17" y="13" width="3" height="3"/><rect x="24" y="13" width="3" height="3"/><rect x="5" y="16" width="3" height="3"/><rect x="5" y="23" width="3" height="3"/><rect x="34" y="20" width="3" height="3"/><rect x="34" y="27" width="3" height="3"/><rect x="19" y="26" width="6" height="8"/></g></svg></div>
    <h3>Office Cleaning<br>Checklist</h3>
    <p>Brightnest cleans your office by following a detailed chelist</p>
  </div>
  <div class="service" style="left:807px">
    <div class="icon"><svg width="46" height="40" viewBox="0 0 46 40"><polygon points="14,8 26,2 26,38 14,38" fill="#111"/><rect x="4" y="16" width="10" height="22" fill="#111"/><rect x="30" y="20" width="12" height="18" fill="#111"/><g fill="#fff"><rect x="17" y="10" width="3" height="3"/><rect x="21" y="10" width="3" height="3"/><rect x="17" y="17" width="3" height="3"/><rect x="21" y="17" width="3" height="3"/><rect x="17" y="24" width="3" height="3"/><rect x="21" y="24" width="3" height="3"/><rect x="7" y="20" width="3" height="3"/><rect x="7" y="27" width="3" height="3"/><rect x="33" y="24" width="3" height="3"/><rect x="37" y="24" width="3" height="3"/></g></svg></div>
    <h3>Commercial<br>Cleaning</h3>
    <p>Brightnest Cleaning and Janitorial Services offers supreme</p>
  </div>
</section>

<section class="welcome">
  <h2 class="abs">Welcome to Lumara Maid Service</h2>
  <p class="abs">Sed ut perspiciatis unde omnis iste natus error sit voluptatem accusantium doloremque laudantium, totam rem aperiam, eaque ipsa quae ab illo inventore veritatis et quasi architecto beatae vitae dicta sunt explicabo.</p>
</section>
<aside class="abs finder">
  <h3>Find Your Local Lumara Maid<br>Service now</h3>
  <div class="postcode">Postcode</div>
  <div class="go">Go</div>
</aside>
<div class="abs rule"></div>

<h2 class="abs recent-title">Recent Services</h2>
<article class="card" style="left:180px"><div class="photo" role="img" aria-label="Cleaner mopping a bright office floor"></div><h4>Cleaning company</h4><span>jun 23, 2014</span></article>
<article class="card" style="left:394px"><div class="photo" role="img" aria-label="Cleaner using a floor polishing machine in an apartment"></div><h4>Cleaning Apartment</h4><span>jun 23, 2014</span></article>
<article class="card" style="left:609px"><div class="photo" role="img" aria-label="Cleaner mopping a house hallway"></div><h4>Cleaning House</h4><span>jun 23, 2014</span></article>
<article class="card" style="left:823px"><div class="photo" role="img" aria-label="Floor scrubbing machine on a wet floor"></div><h4 style="margin-left:3px">Cleaning Company</h4><span style="margin-left:3px">jun 23, 2014</span></article>

<footer class="abs site-footer">
  <nav class="foot-nav">
    <a class="current" href="#" style="left:180px">Home</a>
    <a href="#" style="left:270px">About us</a>
    <a href="#" style="left:376px">Services</a>
    <a href="#" style="left:478px">Recent News</a>
    <a href="#" style="left:606px">Contact</a>
  </nav>
  <div class="abs copyright">© 2014 Lumara Maid Service. All Rights Reserved</div>
  <span class="social" style="left:895px"></span>
  <span class="social" style="left:927px"></span>
  <span class="social" style="left:958px"></span>
  <span class="social" style="left:990px"></span>
</footer>

</body>
</html>
```